Private lender of mortgages and rent to own housing

need a website that reflects real estate especially mortgage lending and rent to own houses..
Sections as follows
Home About Types of mortgages Rent to own Contact us
Target Market(s)
consumers who require non traditonal mortgages
Industry/Entity Type
Mortgage
Coding
Coded - Design and coding required
Number of Pages Required
4 page
Font styles to use
Sans Serif
Colors
Designer to choose colors to be used in the design.
Requirements
Must have
- background pictures on pages. with nice picture on homepage of houses or a community
Nice to have
- contact us form i supplied a ink to

```html
<!DOCTYPE html>
<html lang="en">
<head>
<meta charset="utf-8">
<title>Maple Ridge Lending – Rent to Own a Home</title>
<link rel="stylesheet" href="https://fonts.googleapis.com/css2?family=Open+Sans:wght@400;600;700&family=Roboto:wght@400;500;700&display=swap">
<style>
:root{
  --navy:#2c2663;
  --navy-deep:#221d52;
  --ink:#222222;
  --body:#555555;
  --muted:#777777;
  --grey-bg:#f2f2f2;
  --line:#d9d9d9;
  --white:#ffffff;
}
*{margin:0;padding:0;box-sizing:border-box}
html,body{width:1200px;height:3147px;overflow:hidden;background:var(--white)}
body{position:relative;font-family:"Open Sans",Arial,sans-serif;color:var(--ink)}
.abs{position:absolute}

/* top strip + header */
.top-strip{left:0;top:0;width:1200px;height:6px;background:var(--navy)}
.account-tab{top:0;height:22px;background:var(--navy);color:var(--white);font-size:11px;display:flex;align-items:center;justify-content:center;gap:5px;clip-path:polygon(0 0,100% 0,92% 100%,8% 100%)}
.tab-register{left:898px;width:114px}
.tab-login{left:1020px;width:76px}
.header{left:0;top:6px;width:1200px;height:86px;border-bottom:1px solid #e6e6e6}
.brand{display:flex;align-items:center;gap:8px;font-family:"Open Sans",Arial,sans-serif;font-weight:700;color:var(--navy);text-transform:uppercase;letter-spacing:.3px;white-space:nowrap}
.brand-mark{width:12px;height:12px;background:var(--navy)}
.header-brand{left:96px;top:50px;font-size:14px}
.main-nav{left:0;top:44px;width:1200px;height:20px;font-family:"Roboto",Arial,sans-serif;font-size:15px;font-weight:500;color:var(--ink)}
.main-nav a{position:absolute;color:inherit;text-decoration:none;white-space:nowrap}
.main-nav a.current{color:var(--navy)}

/* hero */
.hero{left:0;top:92px;width:1200px;height:456px;background:linear-gradient(180deg,#7fa3cf 0%,#9fb8d4 22%,#6b6a66 40%,#5c5a55 62%,#8a8f78 80%,#6f8a4f 100%)}
.hero-shade{left:0;top:92px;width:1200px;height:456px;background:rgba(20,20,40,.18)}
.hero-title{left:0;top:222px;width:1200px;text-align:center;font-family:"Roboto",Arial,sans-serif;font-weight:500;font-size:50px;color:var(--white);letter-spacing:.5px}
.hero-sub{left:0;top:287px;width:1200px;text-align:center;font-size:22px;font-weight:700;color:var(--white)}
.btn{display:flex;align-items:center;justify-content:center;background:var(--navy);color:var(--white);border-radius:22px;font-size:14px;font-weight:600;text-transform:uppercase;letter-spacing:.3px;white-space:nowrap}
.hero-btn{left:527px;top:330px;width:147px;height:40px}
.arrow{width:30px;height:50px}

/* about */
.about-frame{left:487px;top:669px;width:610px;height:319px;border:3px solid var(--navy);border-left:none}
.about-frame-left{left:487px;top:957px;width:3px;height:31px;background:var(--navy)}
.about-photo{left:99px;top:625px;width:470px;height:332px;background:linear-gradient(135deg,#c9cdd6 0%,#e8e8ea 45%,#d8b68a 75%,#aeb6c3 100%)}
.about-title{left:627px;top:718px;font-family:"Roboto",Arial,sans-serif;font-size:30px;font-weight:500;color:var(--ink)}
.about-text{left:627px;top:777px;width:430px;font-size:13px;line-height:1.55;color:var(--body)}
.about-btn{left:627px;top:883px;width:147px;height:44px}

/* features */
.features{left:0;top:1076px;width:1200px;height:607px;background:var(--grey-bg)}
.feature{width:300px;text-align:center}
.feature-icon{width:70px;height:70px;border-radius:50%;margin:0 auto;display:flex;align-items:center;justify-content:center;border:2px solid #cfcfcf;background:var(--white)}
.feature-icon.filled{background:var(--navy);border-color:var(--navy)}
.feature h3{font-family:"Open Sans",Arial,sans-serif;font-weight:600;font-size:18px;color:var(--ink);margin-top:16px}
.feature p{font-size:12.5px;line-height:1.6;color:var(--muted);margin-top:6px}
.agent-heading{left:766px;top:1156px;width:333px;text-align:center;font-family:"Roboto",Arial,sans-serif;font-weight:500;font-size:29px;color:var(--ink)}
.agent-card{left:766px;top:1206px;width:333px;height:393px;border:1px solid #bdbdbd;background:linear-gradient(180deg,#efefef 0%,#dadde3 55%,#b9bfca 100%)}
.agent-info{left:767px;top:1483px;width:331px;height:115px;background:rgba(90,90,90,.85);color:var(--white);text-align:center}
.agent-name{font-weight:700;font-size:16px;margin-top:15px}
.agent-line{font-size:12px;display:flex;align-items:center;justify-content:center;gap:7px;margin-top:8px}

/* photos */
.photos-title{left:99px;top:1876px;font-family:"Roboto",Arial,sans-serif;font-weight:500;font-size:29px;color:var(--ink)}
.photos-text{left:99px;top:1927px;width:325px;font-size:12.5px;line-height:1.6;color:var(--body)}
.photos-text p+p{margin-top:8px}
.photos-btn{left:101px;top:2039px;width:115px;height:34px;font-size:13px}
.photo{width:315px;height:206px}
.photo-a{left:453px;top:1765px;background:linear-gradient(180deg,#56508a 0%,#4a4680 60%,#3f3b70 100%)}
.photo-b{left:787px;top:1765px;background:linear-gradient(135deg,#c97e52 0%,#e0c6a6 50%,#8a5a3b 100%)}
.photo-c{left:453px;top:1987px;background:linear-gradient(135deg,#e6e6e6 0%,#c9c3bd 50%,#b44a3d 100%)}
.photo-d{left:787px;top:1987px;background:linear-gradient(135deg,#a89a86 0%,#7a5a40 50%,#c9a53a 100%)}
.photo-link{left:590px;top:1847px;width:40px;height:40px;border-radius:50%;background:rgba(255,255,255,.85);display:flex;align-items:center;justify-content:center}

/* testimonial */
.testimonial{left:0;top:2279px;width:1200px;height:482px;background:radial-gradient(ellipse at 30% 80%,#4a4390 0%,#3a3380 45%,#2e2870 100%)}
.testimonial-title{left:0;top:2350px;width:1200px;text-align:center;font-family:"Roboto",Arial,sans-serif;font-weight:500;font-size:29px;color:var(--white)}
.testimonial-quote{left:165px;top:2433px;width:870px;text-align:center;font-size:14.5px;line-height:1.75;color:var(--white)}
.client-photo{left:548px;top:2535px;width:104px;height:104px;border-radius:50%;border:4px solid var(--white);background:linear-gradient(135deg,#a9796a 0%,#5a3e35 100%)}
.client-name{left:0;top:2657px;width:1200px;text-align:center;font-weight:600;font-size:16px;color:var(--white)}

/* footer */
.footer-brand{left:101px;top:2880px;font-size:16px}
.footer-heading{top:2848px;font-family:"Open Sans",Arial,sans-serif;font-weight:700;font-size:15px;color:var(--ink);text-transform:uppercase;white-space:nowrap}
.footer-list{top:2882px;list-style:none;font-size:13px;color:var(--body)}
.footer-list li{height:27px;display:flex;align-items:center;gap:6px;white-space:nowrap}
.social-dot{width:12px;height:12px;background:var(--navy);border-radius:2px}
.field{left:848px;width:214px;height:30px;border:1px solid #bdbdbd;font-size:12px;color:#999;padding-left:8px;display:flex;align-items:center}
.submit-btn{left:990px;top:2965px;width:72px;height:21px;font-size:10px;border-radius:11px}
.footer-rule{left:95px;top:3059px;width:1010px;height:1px;background:var(--line)}
.copyright{left:0;top:3093px;width:1200px;text-align:center;font-size:11px;color:var(--muted)}
</style>
</head>
<body>

<div class="abs top-strip"></div>
<div class="abs account-tab tab-register">
  <svg width="10" height="10" viewBox="0 0 10 10"><rect x="1" y="1" width="8" height="8" fill="none" stroke="#fff" stroke-width="1.2"/><path d="M3 7 L7 3" stroke="#fff" stroke-width="1.2"/></svg>Register</div>
<div class="abs account-tab tab-login">
  <svg width="10" height="10" viewBox="0 0 10 10"><circle cx="5" cy="3.2" r="2.2" fill="#fff"/><path d="M1 10 Q5 4 9 10Z" fill="#fff"/></svg>Login</div>

<header class="abs header"></header>
<div class="abs brand header-brand"><span class="brand-mark"></span>Maple Ridge Lending</div>
<nav class="abs main-nav">
  <a class="current" style="left:504px">Home</a>
  <a style="left:598px">About</a>
  <a style="left:693px">Types of mortgages</a>
  <a style="left:888px">Rent to own</a>
  <a style="left:1025px">Contact us</a>
</nav>

<section>
  <div class="abs hero" role="img" aria-label="Photo of a grey two-storey family house with a garden and driveway"></div>
  <div class="abs hero-shade"></div>
  <h1 class="abs hero-title">RENT TO OWN A HOME</h1>
  <p class="abs hero-sub">We Can Put You in Your Own Home Today</p>
  <a class="abs btn hero-btn">Read More</a>
  <svg class="abs arrow" style="left:18px;top:280px" viewBox="0 0 30 50"><path d="M22 6 L8 25 L22 44" fill="none" stroke="#fff" stroke-width="3"/></svg>
  <svg class="abs arrow" style="left:1152px;top:280px" viewBox="0 0 30 50"><path d="M8 6 L22 25 L8 44" fill="none" stroke="#fff" stroke-width="3"/></svg>
</section>

<section>
  <div class="abs about-frame"></div>
  <div class="abs about-frame-left"></div>
  <div class="abs about-photo" role="img" aria-label="Photo of people signing a mortgage contract beside a small model house"></div>
  <h2 class="abs about-title">About Us</h2>
  <p class="abs about-text">We know life sometimes delivers challenges and it can be hard to get back on track once you have dealt with challenges. Maybe you have been through a divorce, bankruptcy, consumer proposal, loss of job, work place injury, new to the country.</p>
  <a class="abs btn about-btn">Read More</a>
</section>

<section>
  <div class="abs features"></div>

  <div class="abs feature" style="left:77px;top:1226px">
    <div class="feature-icon filled">
      <svg width="34" height="34" viewBox="0 0 34 34"><rect x="5" y="10" width="24" height="14" rx="2" fill="none" stroke="#fff" stroke-width="2"/><circle cx="17" cy="17" r="3.5" fill="none" stroke="#fff" stroke-width="2"/></svg>
    </div>
    <h3>Down Payment</h3>
    <p>We focus on rent to own in Simcoe County<br>and our Renting Program.</p>
  </div>
  <div class="abs feature" style="left:383px;top:1226px">
    <div class="feature-icon">
      <svg width="34" height="34" viewBox="0 0 34 34"><path d="M9 17 L17 9 L25 17 M12 15 V25 H22 V15" fill="none" stroke="#2c2663" stroke-width="2"/><path d="M5 28 H29" stroke="#2c2663" stroke-width="2"/></svg>
    </div>
    <h3>Household Income</h3>
    <p>We focus on rent to own in Simcoe County<br>and our Renting Program.</p>
  </div>
  <div class="abs feature" style="left:77px;top:1423px">
    <div class="feature-icon">
      <svg width="34" height="34" viewBox="0 0 34 34"><rect x="9" y="7" width="16" height="21" rx="1" fill="none" stroke="#2c2663" stroke-width="2"/><path d="M12 13 H22 M12 17 H22 M12 21 H19" stroke="#2c2663" stroke-width="2"/></svg>
    </div>
    <h3>Credit Report</h3>
    <p>We focus on rent to own in Simcoe County<br>and our Renting Program.</p>
  </div>
  <div class="abs feature" style="left:383px;top:1423px">
    <div class="feature-icon">
      <svg width="34" height="34" viewBox="0 0 34 34"><path d="M6 28 V15 L13 9 L20 15 V28 Z M20 28 V12 H28 V28" fill="none" stroke="#2c2663" stroke-width="2"/><rect x="11" y="19" width="4" height="4" fill="#2c2663"/></svg>
    </div>
    <h3>Selecting a House</h3>
    <p>We focus on rent to own in Simcoe County<br>and our Renting Program.</p>
  </div>

  <h2 class="abs agent-heading">Our Agent</h2>
  <div class="abs agent-card" role="img" aria-label="Portrait photo of the agent in a grey blazer"></div>
  <div class="abs agent-info">
    <div class="agent-name">Elena Marsh</div>
    <div class="agent-line"><svg width="11" height="11" viewBox="0 0 12 12"><path d="M2 1 L4.5 1 L5.5 4 L4 5 Q5 7.5 7 8 L8 6.5 L11 7.5 L11 10 Q10 11 8 11 Q1 9 1 3 Q1 1 2 1Z" fill="#fff"/></svg><b>(+1) 555-010-0199</b></div>
    <div class="agent-line"><svg width="12" height="10" viewBox="0 0 12 10"><rect x="0.5" y="0.5" width="11" height="9" fill="#fff"/><path d="M0.5 0.5 L6 5.5 L11.5 0.5" fill="none" stroke="#5a5a5a" stroke-width="1"/></svg>hello@mapleridgelending.ca</div>
  </div>
</section>

<section>
  <h2 class="abs photos-title">Latest Photos</h2>
  <div class="abs photos-text">
    <p>May not seem like a strong determining factor overall for qualifying for rent to own but it is for us.</p>
    <p>Although your credit won't necessarily disqualify you from our rent to own program, it is important</p>
  </div>
  <a class="abs btn photos-btn">View All</a>
  <div class="abs photo photo-a" role="img" aria-label="Photo of a large house at dusk"></div>
  <div class="abs photo-link"><svg width="20" height="20" viewBox="0 0 20 20"><rect x="2" y="7" width="9" height="6" rx="3" transform="rotate(-45 6.5 10)" fill="none" stroke="#2c2663" stroke-width="2"/><rect x="9" y="7" width="9" height="6" rx="3" transform="rotate(-45 13.5 10)" fill="none" stroke="#2c2663" stroke-width="2"/></svg></div>
  <div class="abs photo photo-b" role="img" aria-label="Photo of house keys being handed over across a desk"></div>
  <div class="abs photo photo-c" role="img" aria-label="Photo of an advisor meeting with an older couple"></div>
  <div class="abs photo photo-d" role="img" aria-label="Photo of a young couple smiling at a table"></div>
</section>

<section>
  <div class="abs testimonial" role="img" aria-label="Photo of a hand holding house keys, tinted deep blue"></div>
  <h2 class="abs testimonial-title">See Our Clients Words</h2>
  <p class="abs testimonial-quote">Eligibility for construction will vary, but typically we will provide these types of loans will have an approval process that goes beyond the scope of a typical mortgage.Eligibility for construction will vary, but typically we will provide these types of loans will have an approval process that goes beyond the scope of a typical mortgage.</p>
  <svg class="abs arrow" style="left:22px;top:2495px" viewBox="0 0 30 50"><path d="M22 6 L8 25 L22 44" fill="none" stroke="#fff" stroke-width="3"/></svg>
  <svg class="abs arrow" style="left:1148px;top:2495px" viewBox="0 0 30 50"><path d="M8 6 L22 25 L8 44" fill="none" stroke="#fff" stroke-width="3"/></svg>
  <div class="abs client-photo" role="img" aria-label="Client portrait photo"></div>
  <div class="abs client-name">- Dana Whitfield</div>
</section>

<footer>
  <div class="abs brand footer-brand"><span class="brand-mark"></span>Maple Ridge Lending</div>

  <h4 class="abs footer-heading" style="left:413px">Links</h4>
  <ul class="abs footer-list" style="left:413px">
    <li>Home</li><li>About</li><li>Types of mortgages</li><li>Rent to own</li><li>Contact us</li>
  </ul>

  <h4 class="abs footer-heading" style="left:604px">Connect With Us</h4>
  <ul class="abs footer-list" style="left:604px">
    <li><span class="social-dot"></span>Community</li>
    <li><span class="social-dot"></span>Reviews</li>
    <li><span class="social-dot"></span>Videos</li>
    <li><span class="social-dot"></span>News Feed</li>
    <li><span class="social-dot"></span>Updates</li>
  </ul>

  <h4 class="abs footer-heading" style="left:848px">Keep In Touch</h4>
  <div class="abs field" style="top:2885px">Name</div>
  <div class="abs field" style="top:2919px">Email</div>
  <a class="abs btn submit-btn">Submit</a>

  <div class="abs footer-rule"></div>
  <p class="abs copyright">Copyrights © 2017 Maple Ridge Lending. All rights reserved.</p>
</footer>

</body>
</html>
```